web page design with coding

We are a start up insurance agency who needs to design a full functional web page. we recently did a postcard design though drawkettle I will upload the final project for you to see the color scheme/font we would like to continue to use. I also have a rough draft of verbage I would like our website to have. I will upload that as well.

Reason: I am sorry but the person who will make the final decision on the website is out of the country at the moment and will make the final decision when he returns.

Industry/Entity Type

Insurance

Coding

Coded - Design and coding required

```html
<!DOCTYPE html>
<html lang="en">
<head>
<meta charset="utf-8">
<title>Brenwick Insurance Group</title>
<link rel="stylesheet" href="https://fonts.googleapis.com/css2?family=Open+Sans:wght@400;600;700&family=Lato:wght@700&display=swap">
<style>
:root{
  --navy:#173a6e;
  --green:#2e7d45;
  --grey-bg:#f2f2f2;
  --text:#555;
  --dark:#222;
  --contact-bg:#26263d;
  --white:#fff;
}
*{box-sizing:border-box;margin:0;padding:0}
html,body{width:1200px;height:2228px;overflow:hidden;background:var(--white)}
body{position:relative;font-family:"Open Sans",sans-serif;color:var(--dark)}
.abs{position:absolute}

/* header */
.site-header{position:absolute;left:0;top:0;width:1200px;height:107px;background:var(--white)}
.brand{left:100px;top:15px;width:133px;height:79px;border:1px solid #888;background:#e9e9e9;display:flex;align-items:center;justify-content:center;text-align:center;font-weight:700;font-size:15px;line-height:19px;color:var(--dark);padding:4px}
.social{left:836px;top:28px;display:flex;gap:14px}
.social span{width:14px;height:14px;border-radius:50%;background:var(--dark);display:block}
.call{left:972px;top:20px;display:flex;align-items:center;gap:8px}
.call small{display:block;font-size:8px;color:#888;letter-spacing:.5px}
.call strong{display:block;font-size:15px;color:var(--navy);letter-spacing:.5px}
.main-nav{left:410px;top:67px;display:flex;gap:9px}
.main-nav a{display:block;height:30px;line-height:28px;border:1px solid #444;padding:0 12px;font-size:12px;color:var(--dark);text-decoration:none;background:var(--white)}
.main-nav a.active{background:var(--green);border-color:var(--green);color:var(--white)}

/* hero */
.hero{left:0;top:107px;width:1200px;height:680px;overflow:hidden;z-index:2}
.hero-photo{position:absolute;left:0;top:0;width:1200px;height:680px;background:linear-gradient(110deg,#6f8a3c 0%,#c9b46b 30%,#e8dcb0 50%,#a9b86a 70%,#557a34 100%)}
.hero-curve{position:absolute;left:0;top:0}
.slider-arrow{width:46px;height:46px;border-radius:50%;background:rgba(255,255,255,.35);display:flex;align-items:center;justify-content:center}
.welcome-box{left:111px;top:266px;width:367px;height:181px;background:rgba(85,85,85,.82);color:var(--white);padding:36px 35px 0}
.welcome-box h2{font-family:"Lato",sans-serif;font-size:21px;letter-spacing:.3px}
.welcome-box p{font-size:14.5px;line-height:21px;margin-top:14px;color:#eee}
.book-bar{left:111px;top:447px;width:367px;height:70px;background:var(--navy);color:var(--white);display:flex;align-items:center;padding-left:30px;gap:12px}
.book-bar small{font-size:8px;font-weight:700;line-height:11px}
.book-bar strong{font-size:25px;font-weight:600;margin-left:14px}

/* intro */
.intro{left:0;top:772px;width:1200px;height:327px;background:var(--grey-bg);text-align:center}
.section-title{font-size:32px;font-weight:600;color:var(--navy)}
.intro .section-title{position:absolute;left:0;width:1200px;top:29px}
.intro p{position:absolute;left:117px;top:92px;width:966px;font-size:11.8px;line-height:20.8px;color:var(--text)}
.btn-row{position:absolute;left:0;width:1200px;top:226px;display:flex;justify-content:center;gap:3px}
.btn{display:block;height:34px;line-height:34px;width:119px;color:var(--white);font-size:11px;font-weight:700;text-decoration:none;letter-spacing:.4px}
.btn-green{background:var(--green)}
.btn-navy{background:var(--navy)}

/* services */
.services{left:0;top:1099px;width:1200px;height:505px;background:var(--white);text-align:center}
.services .section-title{position:absolute;left:0;width:1200px;top:36px}
.service-card{top:105px;width:312px}
.service-card .photo{width:312px;height:233px;border:2px solid #ddd;box-shadow:0 8px 10px -6px rgba(0,0,0,.35)}
.service-card h3{font-size:19px;font-weight:600;margin-top:20px;letter-spacing:.3px}

/* contact */
.contact{left:0;top:1604px;width:1200px;height:557px;background:var(--contact-bg)}
.contact-map{position:absolute;left:0;top:0;width:1200px;height:557px;background:linear-gradient(135deg,#2b2b44,#222238 60%,#2a2a42)}
.contact .section-title{position:absolute;left:0;width:1200px;top:50px;text-align:center;color:var(--white);font-weight:400;font-size:29px}
.field{border:2px solid #cfcfd6;height:60px;color:var(--white);font-size:21px;padding-left:88px;line-height:56px}
.field-icon{width:56px;height:59px;background:var(--green);display:flex;align-items:center;justify-content:center}
.send-btn{left:936px;top:423px;width:142px;height:55px;background:var(--navy);color:var(--white);font-size:25px;text-align:center;line-height:55px;letter-spacing:.5px}

/* footer */
.site-footer{left:0;top:2161px;width:1200px;height:67px;background:var(--navy);color:var(--white);text-align:center;line-height:67px;font-size:16px;font-weight:600}
</style>
</head>
<body>

<header class="site-header">
  <div class="abs brand">Brenwick Insurance Group</div>
  <div class="abs social" aria-label="Social links"><span></span><span></span><span></span><span></span></div>
  <div class="abs call">
    <svg width="14" height="22" viewBox="0 0 14 22"><path d="M3 1h3l1 5-2 1q1 5 4 8l2-1 2 4-2 2Q5 20 2 10 1 4 3 1z" fill="#173a6e"/></svg>
    <div><small>CALL US NOW</small><strong>555-014-2286</strong></div>
  </div>
  <nav class="abs main-nav">
    <a class="active" href="#" style="width:77px;text-align:center">Home</a>
    <a href="#" style="width:77px;text-align:center">About</a>
    <a href="#">Product &amp; Services</a>
    <a href="#">Business Insurance</a>
    <a href="#">Personal Insurance</a>
    <a href="#">Contact Us</a>
  </nav>
</header>

<section class="abs hero">
  <div class="hero-photo" role="img" aria-label="Happy family of four playing together in a sunny park"></div>
  <svg class="hero-curve" width="1200" height="680" viewBox="0 0 1200 680">
    <path d="M0,524 Q560,751 1200,546 L1200,680 L0,680 Z" fill="#f2f2f2"/>
    <path d="M0,465 Q560,700 1200,500 L1200,546 Q560,751 0,524 Z" fill="#2e7d45"/>
    <path d="M238,621 Q760,710 1200,480 L1200,546 Q760,749 238,628 Z" fill="#173a6e"/>
  </svg>
  <div class="abs slider-arrow" style="left:19px;top:241px"><svg width="12" height="20"><path d="M10 2 2 10l8 8" stroke="#fff" stroke-width="2" fill="none"/></svg></div>
  <div class="abs slider-arrow" style="left:1125px;top:241px"><svg width="12" height="20"><path d="M2 2l8 8-8 8" stroke="#fff" stroke-width="2" fill="none"/></svg></div>
  <div class="abs welcome-box">
    <h2>WELCOME TO BRENWICK</h2>
    <p>Established in 2015, Brenwick Insurance Group is a full service independent insurance agency.</p>
  </div>
  <div class="abs book-bar">
    <svg width="22" height="22" viewBox="0 0 22 22"><rect width="22" height="22" rx="4" fill="#fff"/><path d="M6 4h3l1 4-2 1q1 3 3 5l1-2 4 1v3l-2 2Q9 17 5 8z" fill="#173a6e"/></svg>
    <small>BOOK THROUGH<br>CALL NOW</small>
    <strong>(555)-014-7730</strong>
  </div>
</section>

<section class="abs intro">
  <h2 class="section-title">Welcome To Our Site</h2>
  <p>Brenwick Insurance Group has joined with regional &amp; national insurance companies to provide quality products and superior service. We take the time to discuss options and coverages, not to just sell insurance products. We strive to educate you in the decision making process to become an informed consumer. We specialize in commercial business &amp; personal insurance. We are committed to providing personal attention to all your insurance needs. At Brenwick Insurance Group, we are independent insurance agents. As independent agents, we do not work for any one insurance company; we sell coverage from several different companies. This allows us to focus on providing you with the right amount of insurance and the right type of coverage for your unique needs.</p>
  <div class="btn-row">
    <a class="btn btn-green" href="#">READ MORE</a>
    <a class="btn btn-navy" href="#">CONTACT NOW</a>
  </div>
</section>

<section class="abs services">
  <h2 class="section-title">Our Services</h2>
  <svg class="abs" style="left:52px;top:203px" width="20" height="40"><path d="M18 2 2 20l16 18" stroke="#999" stroke-width="2" fill="none"/></svg>
  <svg class="abs" style="left:1110px;top:203px" width="20" height="40"><path d="M2 2l16 18L2 38" stroke="#999" stroke-width="2" fill="none"/></svg>
  <div class="abs service-card" style="left:99px">
    <div class="photo" role="img" aria-label="Businessman with umbrella against rising chart lines" style="background:linear-gradient(135deg,#3e5866,#9fb5bd)"></div>
    <h3>Business Insurance</h3>
  </div>
  <div class="abs service-card" style="left:436px">
    <div class="photo" role="img" aria-label="Agent reviewing a policy with a couple" style="background:linear-gradient(135deg,#d9d4cc,#8a8580)"></div>
    <h3>Personal Insurance</h3>
  </div>
  <div class="abs service-card" style="left:773px">
    <div class="photo" role="img" aria-label="Home insurance form with model house and calculator" style="background:linear-gradient(135deg,#3d6f8f,#c9c2b4)"></div>
    <h3>Home Insurance</h3>
  </div>
</section>

<section class="abs contact">
  <div class="contact-map" role="img" aria-label="Faint dark city street map background"></div>
  <h2 class="section-title">Contact Us</h2>

  <div class="abs field" style="left:126px;top:166px;width:462px">Name</div>
  <div class="abs field-icon" style="left:137px;top:156px"><svg width="20" height="22"><circle cx="10" cy="6" r="5" fill="#fff"/><path d="M1 21q0-9 9-9t9 9z" fill="#fff"/></svg></div>

  <div class="abs field" style="left:126px;top:252px;width:462px">Email</div>
  <div class="abs field-icon" style="left:137px;top:242px"><svg width="24" height="18"><rect width="24" height="18" rx="2" fill="#fff"/><path d="M1 2l11 8 11-8" stroke="#2e7d45" stroke-width="2" fill="none"/></svg></div>

  <div class="abs field" style="left:126px;top:338px;width:462px">Subject</div>
  <div class="abs field-icon" style="left:137px;top:328px"><svg width="22" height="22"><path d="M20 2Q11 3 6 11l5 5q8-5 9-14zM5 13l-3 7 7-3z" fill="#fff"/></svg></div>

  <div class="abs field" style="left:616px;top:166px;width:462px">Address</div>
  <div class="abs field-icon" style="left:627px;top:156px"><svg width="22" height="22"><circle cx="11" cy="11" r="10" fill="#fff"/><path d="M6 6q4 2 3 6t4 6M14 4q-1 4 4 6" stroke="#2e7d45" stroke-width="2" fill="none"/></svg></div>

  <div class="abs field" style="left:616px;top:252px;width:462px;height:146px">Message</div>
  <div class="abs field-icon" style="left:627px;top:242px"><svg width="22" height="22"><rect x="1" y="4" width="16" height="16" rx="2" stroke="#fff" stroke-width="2" fill="none"/><path d="M8 14l1-4 9-9 3 3-9 9z" fill="#fff"/></svg></div>

  <div class="abs send-btn">SEND</div>
</section>

<footer class="abs site-footer">© Copyright 2016.yoursite. All rights reserved.</footer>

</body>
</html>
```